New Website Announcement

We need a flyer to announce our new website to customers and prospective clients. The website will be launching soon, but I can provide a detailed outline in PDF form with copy and imagery to serve as inspiration for this design.

I would like a postcard size document that can be mailed in an envelope (no need for postcard style mailer info on 1 side)

About my company:

Verity Lane Studio is a new breed of marketing consulting agency built for the next frontier of consumer learning. Social interaction will be at the heart of great insights going forward – in how consumers engage with brands and in how organizations socialize what they learn to gain competitive advantage.
By fusing innovative insights techniques, technology and compelling graphic design-based reporting, we ensure results get noticed and make an impact.

contact info that can also be included:

Email: marek@veritylane-studio.net

Phone: 518-732-5164

Thanks

Attention all designers submitting a design for this project. Please keep in mind a few important details about this project.

1. Remember that the main objective of this postcard is to announce my new website.

2. Please be sure to read the brief for the copy I would like on each side. You can be creative in how it is displayed, but I need this key information somewhere. All other copy on the attached files is for your background only.

3. Please do not submit overly simple designs that just take the images I provided and overlay a text box with my copy. I could easily do this myself in PowerPoint in 5 minutes.

4. Remember that the design should be edgy and modern but needs to be professional and speak to a business audience.

Please submit any questions. Thank you for your submissions. 

Marek

Target Market(s)

senior level marketing and research clients at large companies and agencies

Industry/Entity Type

Marketing

Requirements
Must have
• Main message:

Need an engaging way to tell customers and prospective clients that we have a new website and that they should come visit us online to learn more about out services, check out case studies and read about our exciting partnerships.

COPY TO USE - UPDATED

Side 1:
(logo)
Introducing Verity Lane Studio

Let’s talk about taking research out of the dark ages.

Visit our newly launched website to learn how and get in touch.

www.veritylane-studio.net

Side 2
Logo
followed by tagline:
Consumer insights that get noticed.
A leading-edge marketing partnership that really works.

Additional text to use on Side 2:
How we can help...

Think of us as your go-to resource for identifying and incorporating the most innovative and exciting techniques into your research programs. We carefully curate and develop close partnerships with the best of the best - from online qualitative research and mobile ethnography to social media listening and fresh takes on concept testing, we can guide the way.

Plus, we believe that socializing consumer learning is just as critical as gathering it.By taking insights deliverables to the next level – through infographics, videos, magazines,interactive profiles and so much more – we are getting stakeholders excited to engage with research and inspired to take action because of it.
It’s a new way to look at insights from a new type of partner. And, it’s a new way to get the most from your research dollars.
Nice to have
• could incorporate our website main image of the lamp on white brick background which is attached, but not 100% mandatory.
Should not have
• - should not be too playful or young, but needs to be modern and design focused

- should not be cluttered or overly 'salesy'

- needs to be upscale and elegant / compelling and aligned with the look and feel of the website imagery (see attached)

```html
<!DOCTYPE html>
<html lang="en">
<head>
<meta charset="utf-8">
<title>Introducing Verity Lane Studio – Our New Website</title>
<link rel="stylesheet" href="https://fonts.googleapis.com/css2?family=Open+Sans:ital,wght@0,400;0,700;0,800;1,300;1,400;1,600;1,700&display=swap">
<style>
  :root {
    --wall-dark: #3f4042;
    --wall-mid: #8c8d8f;
    --wall-light: #e6e6e4;
    --panel: rgba(255, 255, 255, 0.74);
    --ink-grey: #606163;
    --tagline-grey: #d9d9d9;
    --accent-red: #c8102e;
    --brand-blue: #1e88c8;
    --white: #ffffff;
  }
  * { margin: 0; padding: 0; box-sizing: border-box; }
  html, body { width: 1200px; height: 929px; overflow: hidden; background: var(--wall-dark); }
  .postcard {
    position: relative;
    width: 1200px;
    height: 929px;
    overflow: hidden;
    font-family: "Open Sans", Arial, sans-serif;
  }
  .lamp-scene {
    position: absolute;
    inset: 0;
    background:
      radial-gradient(ellipse 520px 380px at 560px 380px, var(--wall-light) 0%, rgba(200,200,198,0.7) 40%, rgba(140,141,143,0) 75%),
      radial-gradient(ellipse 900px 700px at 620px 520px, var(--wall-mid) 0%, var(--wall-dark) 100%);
  }
  .tagline {
    position: absolute;
    top: 46px;
    right: 40px;
    text-align: right;
    font-style: italic;
    font-weight: 300;
    font-size: 31px;
    line-height: 44px;
    color: var(--tagline-grey);
  }
  .help-panel {
    position: absolute;
    top: 198px;
    left: 652px;
    width: 548px;
    height: 405px;
    background: var(--panel);
    padding: 18px 34px 0 30px;
    text-align: right;
    font-style: italic;
    color: var(--ink-grey);
  }
  .help-panel h2 {
    font-size: 24px;
    font-weight: 700;
    color: var(--accent-red);
    margin-bottom: 8px;
  }
  .help-panel p {
    font-size: 13.5px;
    line-height: 20px;
    margin-bottom: 14px;
  }
  .focus {
    position: absolute;
    top: 495px;
    left: 95px;
    width: 400px;
    color: var(--white);
    font-style: italic;
  }
  .focus h3 {
    font-size: 19px;
    font-weight: 600;
    margin-bottom: 18px;
    margin-left: 30px;
  }
  .focus ul {
    list-style: none;
    text-align: right;
    font-size: 16px;
    line-height: 22px;
  }
  .announcement {
    position: absolute;
    left: 48px;
    top: 742px;
    width: 600px;
    color: var(--white);
    font-style: italic;
  }
  .announcement h2 {
    font-size: 21px;
    font-weight: 700;
    line-height: 28px;
  }
  .announcement p {
    font-size: 16px;
    line-height: 22px;
  }
  .web-address {
    position: absolute;
    left: 45px;
    bottom: 40px;
    font-style: italic;
    font-size: 44px;
    font-weight: 400;
    color: var(--white);
  }
  .brand {
    position: absolute;
    right: 40px;
    top: 650px;
    text-align: right;
    font-weight: 800;
    font-size: 74px;
    line-height: 74px;
    color: var(--brand-blue);
    letter-spacing: -1px;
  }
</style>
</head>
<body>
<main class="postcard">
  <div class="lamp-scene" role="img" aria-label="Photograph of a tall arched black floor lamp casting light onto a white-painted brick wall and floor"></div>

  <p class="tagline">Consumer insights that get noticed.<br>A leading-edge marketing partnership that really works.</p>

  <section class="help-panel">
    <h2>How we can help...</h2>
    <p>Think of us as your go-to resource for identifying and incorporating the most innovative and exciting techniques into your research programs. We carefully curate and develop close partnerships with the best of the best – from online qualitative research and mobile ethnography to social media listening and fresh takes on concept testing, we can guide the way.</p>
    <p>Plus, we believe that socializing consumer learning is just as critical as gathering it. By taking insights deliverables to the next level – through infographics, videos, magazines, interactive profiles and so much more – we are getting stakeholders excited to engage with research and inspired to take action because of it.</p>
    <p>It’s a new way to look at insights from a new type of partner. And, it’s a new way to get the most from your research dollars.</p>
  </section>

  <section class="focus">
    <h3>We’re focusing on delivering the...</h3>
    <ul>
      <li>- best research approaches</li>
      <li>- most flexible partnership</li>
      <li>- most impactful analysis</li>
      <li>- most elegant, compelling deliverables<br>that people actually want to read</li>
    </ul>
  </section>

  <section class="announcement">
    <h2>Introducing Verity Lane Studio</h2>
    <p>Let’s talk about taking research out of the dark ages. Visit our newly launched website to learn how and get in touch.</p>
  </section>

  <p class="web-address">www.veritylane-studio.net</p>

  <div class="brand">VERITY LANE<br>STUDIO</div>
</main>
</body>
</html>
```